Wordpress Web Design & Coding for velcorahealth.ca

We need a website for a new investment company that is visually grabbing and vibrant. We would like to see a web page that displays trust, growth and confidence. Needs to be responsive and mobile friendly for all browsers and coded for both Android & IOS.

Open to the number of pages and menu items. I selected 4 but if you feel the layout would work better with less I am open to this. Need to sell the people (management team/related businesses) and then show where the invested money will be going (upcoming projects).

Company Info:

Vel Cora is an investment company put together by a group of seasoned business professionals who have come together to combine decades of success in the real estate development, management, financing and medical services. The company will be a full service company offering turn key solutions for medical professionals.

Vel-Cora will focus on providing a full range of services via a group of distinct companies to deliver newly emerging needs of the medical community. The end goal will be to create complete solutions for individuals in the medical community. Our group has experience and success with the conceptualization, construction and financing of medical and dental clinic spaces. Vel-Cora Solutions will be established to accommodate all areas of the development and creation of clinics for medical professionals from building construction to equipment financing and administrations.

You can mention these companies and take photos from their websites. You can also use stock photos.

Our construction partner:
https://318bld.com/projects/

Our equipment leasing partner:
https://www.norvixa.com/

Our Management Team and medical partners

Gil Parish
https://www.ourfirmstance.ca/

Dietmar Vellasquin
https://www.gshdentalservices.com/about-us

PROPOSED PROJECTS (see attachment for details)
Pinegrove Business Park
Holtmere Business Park
Mt. Corwin Ridge Professional

Target Market(s)

Investors

Industry/Entity Type

Investment

Coding

Coded - Design and coding required

Number of Pages Required

4 page

Font styles to use
Sans Serif

Requirements
Must have
• Wordpress – must be both desktop and mobile friendly with fast page load speed
Ability to edit after ourselves in Wordpress
Attractive home page with logo etc.
Logo colours are: for the blue the pantone color is #0355a3
and for the green is #8cc63f

Sections, about us, what we do/services we provide, contact us

```html
<!DOCTYPE html>
<html lang="en">
<head>
<meta charset="utf-8">
<title>Vel-Cora Solutions</title>
<link rel="stylesheet" href="https://fonts.googleapis.com/css2?family=Roboto:wght@400;500&family=Poppins:wght@400;500&family=Open+Sans:wght@300;400&display=swap">
<style>
:root{
  --blue:#0355a3;
  --green:#8cc63f;
  --button-green:#6fb514;
  --ink:#222;
  --body:#3a3a3a;
  --muted:#8a8a8a;
  --band:#eef3f9;
  --footer:#2b2b2b;
  --footer-text:#e6e6e6;
  --white:#fff;
}
*{margin:0;padding:0;box-sizing:border-box}
html,body{width:1200px;height:2733px;overflow:hidden;background:var(--white)}
body{position:relative;font-family:"Open Sans",sans-serif;color:var(--body)}

/* header */
.site-header{position:absolute;left:0;top:0;width:1200px;height:86px;background:var(--white)}
.brand{position:absolute;left:106px;top:28px;display:flex;align-items:center;gap:9px}
.brand-mark{width:16px;height:16px;background:var(--green)}
.brand-name{font-family:"Roboto",sans-serif;font-weight:500;font-size:25px;color:var(--blue);letter-spacing:.5px}
.main-nav a{position:absolute;top:32px;font-family:"Poppins",sans-serif;font-size:14px;color:#555;text-decoration:none}
.main-nav a.active{color:var(--blue)}
.main-nav a.active::after{content:"";position:absolute;left:0;right:0;top:26px;height:2px;background:var(--blue)}
.nav-divider{position:absolute;left:1028px;top:33px;width:2px;height:18px;background:var(--blue)}
.search-icon{position:absolute;left:1052px;top:33px}

/* hero */
.hero{position:absolute;left:0;top:86px;width:1200px;height:600px;
  background:
    radial-gradient(ellipse 260px 330px at 240px 330px,#23252a 0%,rgba(35,37,42,.85) 45%,rgba(35,37,42,0) 100%),
    radial-gradient(ellipse 180px 120px at 170px 170px,rgba(150,110,80,.55),rgba(150,110,80,0) 100%),
    radial-gradient(ellipse 420px 300px at 1130px 520px,rgba(60,140,70,.55),rgba(60,140,70,0) 100%),
    radial-gradient(ellipse 500px 260px at 800px 60px,rgba(230,232,230,.7),rgba(230,232,230,0) 100%),
    linear-gradient(90deg,#5b6670 0%,#7a8590 30%,#a7adae 55%,#8f9797 80%,#6f7a74 100%)}
.hero-copy{position:absolute;left:630px;top:214px;width:470px;text-align:center;color:var(--white)}
.hero-title{font-family:"Roboto",sans-serif;font-weight:500;font-size:53px;letter-spacing:1.5px;line-height:1}
.hero-text{margin-top:12px;font-size:17px;line-height:27px}
.btn{display:inline-block;background:var(--button-green);color:var(--white);font-family:"Poppins",sans-serif;font-size:14px;text-align:center;border-radius:20px;text-decoration:none}
.hero .btn{position:absolute;left:756px;top:351px;width:199px;height:39px;line-height:39px;font-family:"Open Sans",sans-serif;font-size:15px}
.dots{position:absolute;display:flex;gap:8px}
.dot{width:8px;height:8px;border-radius:50%;border:1px solid var(--white)}
.dot.on{background:var(--blue);border-color:var(--blue)}
.dots.dark .dot{border-color:#555}
.dots.dark .dot.on{border-color:var(--blue)}

/* headings */
.section-title{position:absolute;font-family:"Roboto",sans-serif;font-weight:400;color:var(--ink);text-transform:uppercase;white-space:nowrap}
.divider{position:absolute;display:flex;align-items:center;gap:6px}
.divider span{width:58px;height:1px;background:var(--blue)}
.divider i{width:10px;height:10px;background:var(--green)}

/* about */
.about-text{position:absolute;left:113px;top:862px;width:478px;font-size:14px;font-weight:400;line-height:28.4px;text-align:justify;text-align-last:left}
.about .btn{position:absolute;left:112px;top:1080px;width:159px;height:37px;line-height:37px}
.about-photo{position:absolute;left:657px;top:805px;width:429px;height:302px;
  background:
    radial-gradient(ellipse 120px 150px at 150px 190px,rgba(30,38,60,.9),rgba(30,38,60,0) 100%),
    radial-gradient(ellipse 110px 170px at 360px 170px,rgba(70,82,105,.9),rgba(70,82,105,0) 100%),
    radial-gradient(ellipse 60px 60px at 160px 70px,rgba(110,75,55,.7),rgba(110,75,55,0) 100%),
    linear-gradient(180deg,#e4e8eb 0%,#cfd5da 60%,#b9c0c7 100%)}

/* services */
.services-band{position:absolute;left:0;top:1246px;width:1200px;height:683px;background:var(--band)}
.card{position:absolute;top:1401px;width:313px;height:395px;background:var(--white);border-radius:8px;overflow:hidden;box-shadow:0 2px 6px rgba(0,0,0,.05);text-align:center}
.card-photo{height:171px}
.card h3{margin-top:23px;font-family:"Roboto",sans-serif;font-weight:500;font-size:15px;letter-spacing:.8px;color:var(--ink)}
.card p{margin:17px 17px 0;font-family:"Poppins",sans-serif;font-size:12.5px;line-height:21.5px;color:var(--muted);text-align:justify;text-align-last:center}
.card .btn{position:absolute;left:77px;top:331px;width:159px;height:38px;line-height:38px}

/* partners */
.partner-name{position:absolute;text-align:center;font-family:"Roboto",sans-serif;font-weight:500}
.partner-divider{position:absolute;left:605px;top:2130px;width:1px;height:107px;background:#ddd}

/* footer */
.site-footer{position:absolute;left:0;top:2313px;width:1200px;height:420px;background:var(--footer);color:var(--footer-text)}
.footer-brand{position:absolute;left:108px;top:70px;display:flex;align-items:center;gap:9px}
.footer-brand .brand-name{font-size:28px}
.contact-list{position:absolute;left:108px;top:157px;list-style:none;font-family:"Poppins",sans-serif;font-size:10px;color:var(--white)}
.contact-list li{display:flex;align-items:center;gap:14px;height:26.5px}
.social{position:absolute;left:109px;top:275px;display:flex;gap:10px}
.social span{width:34px;height:34px;border-radius:50%;background:#3b3b3b;border:1px solid #5a5a5a;box-shadow:inset 0 0 0 9px #3b3b3b,inset 0 0 0 17px #4a4a4a}
.footer-col{position:absolute;top:104px}
.footer-col h4{font-family:"Roboto",sans-serif;font-weight:500;font-size:17px;color:var(--white);margin-bottom:22px}
.footer-col ul{list-style:none;font-family:"Poppins",sans-serif;font-size:14.5px;color:var(--white)}
.footer-col li{height:31px;display:flex;align-items:center;gap:9px}
.footer-col li::before{content:"";width:4px;height:4px;border-radius:50%;background:var(--green)}
.newsletter p{font-size:13.5px;line-height:17px;color:var(--footer-text);margin-top:-4px}
.subscribe{position:absolute;left:777px;top:208px;display:flex;height:39px}
.subscribe .field{width:209px;background:#3d3d3d;font-family:"Roboto",sans-serif;font-size:13px;color:#aaa;padding:13px 16px}
.subscribe .go{width:100px;background:var(--green);font-family:"Roboto",sans-serif;font-size:13px;color:#1f3b00;text-align:center;line-height:39px}
.footer-rule{position:absolute;left:108px;top:335px;width:978px;height:1px;background:#444}
.copyright{position:absolute;left:0;top:352px;width:1200px;text-align:center;font-size:10px;color:#ddd}
</style>
</head>
<body>

<header class="site-header">
  <div class="brand"><span class="brand-mark"></span><span class="brand-name">VEL-CORA</span></div>
  <nav class="main-nav">
    <a class="active" href="#" style="left:509px">Home</a>
    <a href="#" style="left:583px">About Us</a>
    <a href="#" style="left:677px">Services</a>
    <a href="#" style="left:771px">Partners</a>
    <a href="#" style="left:865px">Blog</a>
    <a href="#" style="left:932px">Contact Us</a>
  </nav>
  <span class="nav-divider"></span>
  <svg class="search-icon" width="18" height="18" viewBox="0 0 18 18" fill="none" stroke="#0355a3" stroke-width="2"><circle cx="7.5" cy="7.5" r="6"/><line x1="12" y1="12" x2="17" y2="17"/></svg>
</header>

<section class="hero" role="img" aria-label="Young professional in a blazer checking his phone in a bright office corridor">
  <div class="hero-copy">
    <h1 class="hero-title">Vel Cora Solutions</h1>
    <p class="hero-text">Ab illo inventore veritatis et quasi architecto beatae vitae atemdicta sunt explicabo Nemo enim ipsam voluptate</p>
  </div>
  <a class="btn" href="#">GET STARTED</a>
  <div class="dots" style="left:580px;top:523px"><span class="dot on"></span><span class="dot"></span><span class="dot"></span></div>
</section>

<section class="about">
  <h2 class="section-title" style="left:112px;top:786px;font-size:30px">About Us</h2>
  <div class="divider" style="left:112px;top:822px"><span style="width:40px"></span><i></i><span style="width:40px"></span></div>
  <p class="about-text">Vel Cora is an investment company put together by a group of seasoned business professionals who have come together to combine decades of success in the real estate development, management, financing and medical services. The company will be a full service company offering turn key solutions for medical professionals.Vel-Cora will focus on providing a full range of services via a group of distinct companies</p>
  <a class="btn" href="#">Read More</a>
  <div class="about-photo" role="img" aria-label="Two business partners smiling during a meeting at a desk"></div>
</section>

<div class="services-band"></div>
<h2 class="section-title" style="left:0;width:1200px;text-align:center;top:1334px;font-size:25px">Our Services</h2>
<div class="divider" style="left:525px;top:1366px"><span></span><i></i><span></span></div>

<article class="card" style="left:110px">
  <div class="card-photo" role="img" aria-label="House keys being handed over to a new owner" style="background:radial-gradient(ellipse 90px 70px at 60px 110px,rgba(30,40,75,.95),rgba(30,40,75,0) 100%),radial-gradient(ellipse 70px 90px at 240px 80px,rgba(200,170,130,.8),rgba(200,170,130,0) 100%),linear-gradient(90deg,#4a5a7a 0%,#9fb0c8 45%,#c9d4e2 70%,#e9e3dc 100%)"></div>
  <h3>REAL ESTATE DEVELOPMENT</h3>
  <p>Lorem ipsum dolor sit amet, erconsectetur adipiscing elit, sed do eiusmod asertempor incididunt ut labore et dolore magna aliqua. Quis ipsum suspendisse.</p>
  <a class="btn" href="#">Read More</a>
</article>
<article class="card" style="left:443px">
  <div class="card-photo" role="img" aria-label="Team members working together in an open office" style="background:radial-gradient(ellipse 90px 80px at 130px 110px,rgba(170,100,40,.95),rgba(170,100,40,0) 100%),radial-gradient(ellipse 70px 70px at 230px 120px,rgba(60,60,65,.7),rgba(60,60,65,0) 100%),linear-gradient(180deg,#cfd2d4 0%,#e6e7e8 50%,#bfc3c6 100%)"></div>
  <h3>MANAGEMENT</h3>
  <p>Lorem ipsum dolor sit amet, erconsectetur adipiscing elit, sed do eiusmod asertempor incididunt ut labore et dolore magna aliqua. Quis ipsum suspendisse.</p>
  <a class="btn" href="#">Read More</a>
</article>
<article class="card" style="left:776px">
  <div class="card-photo" role="img" aria-label="Laptop and tablet showing financial charts on a desk" style="background:radial-gradient(ellipse 100px 60px at 110px 60px,rgba(70,75,85,.8),rgba(70,75,85,0) 100%),radial-gradient(ellipse 80px 50px at 130px 140px,rgba(120,160,200,.6),rgba(120,160,200,0) 100%),linear-gradient(135deg,#d5d9dc,#f1f2f3 50%,#cfd3d6)"></div>
  <h3>FINANCING</h3>
  <p>Lorem ipsum dolor sit amet, erconsectetur adipiscing elit, sed do eiusmod asertempor incididunt ut labore et dolore magna aliqua. Quis ipsum suspendisse.</p>
  <a class="btn" href="#">Read More</a>
</article>
<div class="dots dark" style="left:588px;top:1835px"><span class="dot on"></span><span class="dot"></span></div>

<section class="partners">
  <h2 class="section-title" style="left:0;width:1200px;text-align:center;top:2020px;font-size:25px">Our Construction and Equipment Leasing Partners</h2>
  <div class="divider" style="left:525px;top:2055px"><span></span><i></i><span></span></div>
  <div class="partner-name" style="left:270px;top:2160px;width:290px;font-size:30px;color:#2b3a8c">318 BUILDS INC.</div>
  <span class="partner-divider"></span>
  <div class="partner-name" style="left:655px;top:2160px;width:270px;font-size:22px;color:#8b2a3a">Norvixa Equipment<br>Leasing Inc.</div>
</section>

<footer class="site-footer">
  <div class="footer-brand"><span class="brand-mark"></span><span class="brand-name">VEL-CORA</span></div>
  <ul class="contact-list">
    <li><svg width="9" height="11" viewBox="0 0 9 11"><path d="M4.5 0a4 4 0 0 0-4 4c0 3 4 7 4 7s4-4 4-7a4 4 0 0 0-4-4z" fill="#0355a3"/></svg>2280 Harbor Lane, Alder Bend, TX</li>
    <li><svg width="9" height="9" viewBox="0 0 9 9"><path d="M1 1l2 0 1 2-1 1a5 5 0 0 0 2 2l1-1 2 1v2C4 8 1 5 1 1z" fill="#0355a3"/></svg>555 014 2290</li>
    <li><svg width="10" height="8" viewBox="0 0 10 8" fill="none" stroke="#0355a3"><rect x=".5" y=".5" width="9" height="7"/><path d="M.5.5l4.5 4 4.5-4"/></svg>hello@velcorahealth.ca</li>
  </ul>
  <div class="social" aria-label="Social links"><span></span><span></span><span></span><span></span></div>

  <div class="footer-col" style="left:404px">
    <h4>Quick Links</h4>
    <ul><li>Home</li><li>About Us</li><li>Services</li><li>Partners</li><li>More</li></ul>
  </div>
  <div class="footer-col" style="left:582px">
    <h4>My Account</h4>
    <ul><li>Terms &amp; Conditions</li><li>Disclaimer</li><li>Privacy Policy</li><li>More</li></ul>
  </div>
  <div class="footer-col newsletter" style="left:775px;top:106px">
    <h4>Join Our Newsletter Now</h4>
    <p>Get E-mail updates about our latest shop<br>&amp; Special Offers.</p>
  </div>
  <div class="subscribe"><span class="field">Enter Your Mail</span><span class="go">SUBSCRIBE</span></div>
  <div class="footer-rule"></div>
  <p class="copyright">Copyright ©2020 All rights reserved</p>
</footer>

</body>
</html>
```